Professional Services - letterhead / business cards

The company (velmora partners) will provide services to Investment Funds and large investors in Spain. I have recently chosen a logo that I am attaching.

I would like a simple stationary design that i could use as letter head, business cards and "with compliments" cards.

I am not quite sure which color I will mostly use for the logo, in the email signature I will probably lean towards the white background and grey letters. I am attaching my favourite options.

Target Market(s)

Large Multinationals, Investment funds and Law firms

Industry/Entity Type

Business

Requirements
Must have
• my details are:
Luis R. Abadal
Velmora Partners S.L.
Casa de Torrelumbre
Calle de Vientoalto 27
28014 Madrid
T: +34 (91) 387-2265
M: +34 (646) 819-054
e-mail: labadal@velmorapartners.com

```html
<!DOCTYPE html>
<html lang="es">
<head>
<meta charset="utf-8">
<title>Velmora Partners — business card</title>
<link rel="stylesheet" href="https://fonts.googleapis.com/css2?family=Questrial&display=swap">
<style>
  :root {
    --backdrop: #e9e7e4;
    --card: #ffffff;
    --navy: #26265f;
    --grey: #7a7a7a;
    --rule: #b9b9b9;
    --shadow: rgba(0, 0, 0, 0.18);
  }
  * { margin: 0; padding: 0; box-sizing: border-box; }
  html, body {
    width: 1200px;
    height: 719px;
    overflow: hidden;
    background: var(--backdrop);
    font-family: "Questrial", "Century Gothic", sans-serif;
  }
  .stage {
    position: relative;
    width: 1200px;
    height: 719px;
    display: flex;
    align-items: center;
    justify-content: center;
    gap: 60px;
  }
  .card {
    position: relative;
    width: 520px;
    height: 300px;
    background: var(--card);
    border-radius: 28px;
    box-shadow: 0 10px 24px var(--shadow);
  }
  .wordmark {
    position: absolute;
    color: var(--navy);
    font-size: 38px;
    font-weight: 400;
    letter-spacing: 0.5px;
    white-space: nowrap;
  }
  .card-front .wordmark { left: 40px; top: 52px; }

  .holder {
    position: absolute;
    right: 36px;
    top: 124px;
    text-align: right;
  }
  .holder-name {
    color: var(--navy);
    font-size: 18px;
    letter-spacing: 1.2px;
  }
  .divider {
    position: absolute;
    left: 0;
    right: 28px;
    top: 154px;
    height: 2px;
    background: linear-gradient(to right, rgba(185,185,185,0), var(--rule) 45%, var(--rule));
  }
  .holder-company {
    position: absolute;
    right: 36px;
    top: 162px;
    color: var(--grey);
    font-size: 11px;
  }
  .address {
    position: absolute;
    right: 36px;
    top: 192px;
    text-align: right;
    color: var(--grey);
    font-size: 12px;
    line-height: 1.45;
  }
  .contacts {
    position: absolute;
    left: 40px;
    bottom: 34px;
    list-style: none;
    color: var(--grey);
    font-size: 12px;
  }
  .contacts li {
    display: flex;
    align-items: center;
    gap: 10px;
    height: 22px;
  }
  .contacts svg { width: 12px; height: 12px; fill: var(--navy); flex: none; }

  .card-back .wordmark {
    left: 0;
    right: 0;
    top: 104px;
    text-align: center;
  }
  .web {
    position: absolute;
    left: 0;
    right: 0;
    bottom: 56px;
    text-align: center;
    color: var(--navy);
    font-size: 13px;
    font-weight: 400;
    letter-spacing: 6px;
  }
</style>
</head>
<body>
<main class="stage">
  <section class="card card-front" aria-label="Card front">
    <div class="wordmark">velmora partners</div>

    <div class="holder"><p class="holder-name">Luis R. Abadal</p></div>
    <div class="divider"></div>
    <p class="holder-company">Velmora Partners S.L.</p>

    <address class="address">
      Casa de Torrelumbre<br>
      Calle de Vientoalto 27<br>
      28014 Madrid
    </address>

    <ul class="contacts">
      <li>
        <svg viewBox="0 0 24 24" aria-hidden="true"><path d="M6.6 10.8a15.1 15.1 0 0 0 6.6 6.6l2.2-2.2a1 1 0 0 1 1-.25 11.4 11.4 0 0 0 3.6.57 1 1 0 0 1 1 1V20a1 1 0 0 1-1 1A17 17 0 0 1 3 4a1 1 0 0 1 1-1h3.5a1 1 0 0 1 1 1c0 1.25.2 2.45.57 3.57a1 1 0 0 1-.25 1z"/></svg>
        <span>+34 (91) 387-2265</span>
      </li>
      <li>
        <svg viewBox="0 0 24 24" aria-hidden="true"><path d="M7 1h10a2 2 0 0 1 2 2v18a2 2 0 0 1-2 2H7a2 2 0 0 1-2-2V3a2 2 0 0 1 2-2zm0 3v14h10V4zm5 15.5a1.2 1.2 0 1 0 0 2.4 1.2 1.2 0 0 0 0-2.4z"/></svg>
        <span>+34 (646) 819-054</span>
      </li>
      <li>
        <svg viewBox="0 0 24 24" aria-hidden="true"><path d="M2 5h20v14H2zm2 2v.5l8 5 8-5V7zm0 2.8V17h16V9.8l-8 5z"/></svg>
        <span>labadal@velmorapartners.com</span>
      </li>
    </ul>
  </section>

  <section class="card card-back" aria-label="Card back">
    <div class="wordmark">velmora partners</div>
    <p class="web">www.velmora.com</p>
  </section>
</main>
</body>
</html>
```